Hi Designers,

I will need 4 web pages designed. The web page looks like an App (if you click on the logo, or the icon on an iPad, it will take you to the website), but it is still a webpage.

Please check the attachment on this brief to understand what specific pages I need to be designed.

A .PSD (straight-up PhotoShop image) as final deliverable is fine, as long as you give us the exact “web color numbers”.

The design is for desktop and iPad but in a single unified web application, NOT separate web app and (native) iPad app.

Details:

Brightwater Policy Partners is developing a browser-based application for use on any mobile device or desktop. The app will be used by corporations to communicate with their employees regarding legal, regulatory and company requirements for conducting business. The app is known as “Harbor Guidance Portal.” When the user clicks on the icon for Harbor Guidance Portal, they will enter a site full of information that a company deems necessary for the employee to do his/her job. There are several content sections within the site, including a login page, training, policies, forms, news feeds and blogs.

The application has been built using Microsoft .NET, and fully supports CSS-type skinning; it uses traditional page layouts. We are seeking a product logo concept (image), a master application/desktop icon (image), as well as a full color scheme/theme/skin design for all areas of the application (header area, body text, menu bar, etc.) in the form of a CSS. The look should be clean, crisp and professional; nothing cartoony or whimsical. It should be easy to read and “airy”.

We have sketched prototypes for the basic application page layout that we can send as a next step of the process.
Updates

Screen shots have been uploaded to this project.  Please use them to guide your design.

Dear designers,

I apologize for the delay in providing feedback. My partners and I will provide feedback in a few days. Thank you for your patience.

Industry/Entity Type

Business

Font styles to use
Other font styles liked:
• see font on screen shots when uploaded

```html
<!DOCTYPE html>
<html lang="en">
<head>
<meta charset="utf-8">
<title>Quillane – Sign In</title>
<link rel="stylesheet" href="https://fonts.googleapis.com/css2?family=Open+Sans:wght@400;600;700&display=swap">
<style>
  :root {
    --bg-top: #003366;
    --bg-bottom: #002a56;
    --panel: #0c4680;
    --panel-edge: #1d5890;
    --field: #fbfbfb;
    --field-shade: #e4e4e4;
    --label: #ffffff;
    --muted: #8fb0d2;
    --accent: #f07a2a;
    --button-top: #e66f45;
    --button-bottom: #c0482a;
    --footer-text: #1b4a7c;
    --mark-blue: #2a9fd8;
  }
  * { box-sizing: border-box; margin: 0; padding: 0; }
  html, body { width: 1200px; height: 825px; overflow: hidden; }
  body {
    position: relative;
    font-family: "Open Sans", Arial, sans-serif;
    background: linear-gradient(to bottom, var(--bg-top) 0, var(--bg-top) 437px, var(--bg-bottom) 437px, var(--bg-bottom) 100%);
  }
  .client-brand {
    position: absolute; left: 507px; top: 112px;
    display: flex; align-items: center; gap: 22px;
  }
  .client-brand .brand-dot {
    width: 52px; height: 52px; border-radius: 50%;
    background: var(--mark-blue);
  }
  .client-brand .brand-name { color: var(--label); font-size: 16px; font-weight: 400; }

  .login-panel {
    position: absolute; left: 360px; top: 205px; width: 480px; height: 356px;
    background: var(--panel);
    border: 1px solid var(--panel-edge);
    border-radius: 6px;
  }
  .panel-shadow { position: absolute; left: 380px; top: 560px; width: 440px; height: 36px; }

  .field-row { position: absolute; left: 0; width: 100%; height: 42px; }
  .field-row.username { top: 69px; }
  .field-row.password { top: 142px; }
  .field-label {
    position: absolute; right: 354px; top: 11px;
    color: var(--label); font-size: 15px; letter-spacing: 0.2px;
  }
  .field-input {
    position: absolute; left: 141px; top: 0; width: 290px; height: 42px;
    border: none; border-radius: 8px;
    background: linear-gradient(to bottom, var(--field) 60%, var(--field-shade));
    box-shadow: inset 0 -2px 3px rgba(0,0,0,0.12);
  }
  .options { position: absolute; left: 142px; top: 207px; width: 287px; font-size: 13px; }
  .remember { color: var(--muted); display: flex; align-items: center; gap: 11px; }
  .remember .check {
    width: 11px; height: 11px; background: #d9d9d9; border: 1px solid #aab;
  }
  .forgot { position: absolute; right: 0; top: 0; color: var(--accent); text-decoration: none; }
  .sign-in {
    position: absolute; left: 146px; top: 254px; width: 120px; height: 47px;
    border: none; border-radius: 3px;
    background: linear-gradient(to bottom, var(--button-top), var(--button-bottom));
    color: #fff; font-family: "Open Sans", Arial, sans-serif;
    font-size: 17px; font-weight: 600;
  }

  .product-brand {
    position: absolute; left: 447px; top: 604px;
    display: flex; align-items: center; gap: 17px;
  }
  .product-brand .brand-dot {
    width: 78px; height: 78px; border-radius: 50%;
    background: var(--mark-blue);
  }
  .product-brand .brand-name {
    color: var(--label); font-size: 20px; font-weight: 400;
    line-height: 26px; letter-spacing: 0.4px;
  }
  .copyright {
    position: absolute; left: 0; top: 724px; width: 100%; text-align: center;
    color: var(--footer-text); font-size: 12px; font-weight: 700;
  }
</style>
</head>
<body>
  <header class="client-brand">
    <span class="brand-dot"></span>
    <span class="brand-name">Quillane</span>
  </header>

  <svg class="panel-shadow" viewBox="0 0 440 36" aria-hidden="true">
    <defs>
      <radialGradient id="shade" cx="50%" cy="0%" r="60%">
        <stop offset="0" stop-color="#000" stop-opacity="0.45"/>
        <stop offset="1" stop-color="#000" stop-opacity="0"/>
      </radialGradient>
    </defs>
    <path d="M0 0 Q220 36 440 0 Z" fill="url(#shade)"/>
  </svg>

  <form class="login-panel">
    <div class="field-row username">
      <label class="field-label">USERNAME</label>
      <input class="field-input" type="text">
    </div>
    <div class="field-row password">
      <label class="field-label">PASSWORD</label>
      <input class="field-input" type="password">
    </div>
    <div class="options">
      <span class="remember"><span class="check"></span>Keep me signed in</span>
      <a class="forgot" href="#">Forgot Password ?</a>
    </div>
    <button class="sign-in" type="button">SIGN IN</button>
  </form>

  <div class="product-brand">
    <span class="brand-dot"></span>
    <span class="brand-name">HARBOR GUIDANCE<br>PORTAL</span>
  </div>

  <footer class="copyright">ALL RIGHTS RESERVED. COPYRIGHTS @ 2013 HGP</footer>
</body>
</html>
```